Bork Ventures, Inc. Website redesign

Revamp the website, it is old and outdated. www.borkventuresinc.example

Target Market(s)

Information Technology Consulting and Staffing

Coding

Coded - Design and coding required

Number of Pages Required

5+ page

Colors

Designer to choose colors to be used in the design.

Requirements
Must have
• Outlined text boxes just like from the Tolvane.example site. A clean look

```html
<!DOCTYPE html>
<html lang="en">
<head>
<meta charset="utf-8">
<title>Bork Ventures, Inc.</title>
<link rel="stylesheet" href="https://fonts.googleapis.com/css2?family=Montserrat:wght@500;600;700&family=Lato:wght@400;700&display=swap">
<style>
:root{
  --red:#8c1628;
  --red-bright:#b01c33;
  --ink:#1b1b1b;
  --text:#444;
  --lavender:#dde1ef;
  --footer:#232323;
  --footer-text:#bdbdbd;
  --white:#fff;
}
*{box-sizing:border-box;margin:0;padding:0}
html,body{width:1200px;height:3425px;overflow:hidden}
body{position:relative;background:var(--white);font-family:'Lato',sans-serif;color:var(--text)}
.abs{position:absolute}
.head{font-family:'Montserrat',sans-serif;font-weight:700;text-transform:uppercase;color:var(--ink)}
.btn-outline{position:absolute;display:flex;align-items:center;justify-content:center;border:2px solid var(--red);color:var(--red);font-family:'Montserrat',sans-serif;font-weight:600;font-size:15px;text-transform:uppercase;background:var(--white)}

/* header */
.topbar{left:768px;top:0;width:432px;height:42px;background:#3a3a3a;clip-path:polygon(0 0,100% 0,100% 100%,45px 100%);color:var(--white);font-family:'Montserrat',sans-serif;font-weight:600;font-size:19px;display:flex;align-items:center;padding-left:60px;gap:8px}
.brand{left:133px;top:40px;display:flex;align-items:center;gap:12px;font-family:'Montserrat',sans-serif;font-weight:700;font-size:30px;color:var(--ink)}
.brand-square{width:26px;height:26px;background:var(--red)}
.nav{left:433px;top:68px;display:flex;gap:34px;font-family:'Montserrat',sans-serif;font-weight:600;font-size:15px;color:#222}
.nav .active{color:var(--red-bright)}
.nav-dot{left:447px;top:46px;width:16px;height:16px;background:var(--red-bright)}

/* hero */
.hero{left:0;top:118px;width:1200px;height:593px;background:linear-gradient(90deg,#0c1428 0%,#15264a 40%,#1e4f86 65%,#0e2340 100%)}
.hero-title{left:168px;top:318px;font-family:'Montserrat',sans-serif;font-weight:700;font-size:35px;color:var(--white)}
.hero-sub{left:171px;top:365px;font-family:'Montserrat',sans-serif;font-weight:500;font-size:26px;color:var(--white)}
.hero-btn{left:176px;top:417px;width:170px;height:49px;background:var(--red);color:var(--white);font-family:'Montserrat',sans-serif;font-weight:600;font-size:18px;display:flex;align-items:center;justify-content:center}
.circle-arrow{width:52px;height:52px;border-radius:50%;background:rgba(255,255,255,.25);display:flex;align-items:center;justify-content:center}

/* services */
.band{left:0;top:711px;width:1200px;height:349px;background:linear-gradient(#e3e3e3,#f3f3f3)}
.svc{top:654px;width:281px;height:384px;background:var(--white);border-bottom:3px solid var(--red);box-shadow:0 2px 6px rgba(0,0,0,.12)}
.svc-head{height:73px;background:var(--red);border-top:3px solid var(--red-bright);color:var(--white);font-family:'Montserrat',sans-serif;font-weight:700;font-size:18px;line-height:23px;padding:14px 0 0 24px;text-transform:uppercase}
.svc-img{height:163px}
.svc p{font-size:13px;line-height:17px;color:#333;padding:18px 24px 0 24px;height:80px}
.svc .btn-outline{left:24px;top:324px;width:146px;height:42px;font-size:13px}

/* intro */
.intro-mark{left:574px;top:1118px;width:52px;height:52px;background:var(--red)}
.intro-title{left:0;top:1184px;width:1200px;text-align:center;font-size:27px;line-height:39px}
.intro-text{left:230px;top:1280px;width:740px;text-align:center;font-size:18px;line-height:26px;color:#444}

/* strategy */
.strategy{left:0;top:1519px;width:1200px;height:521px;background:var(--lavender)}
.strategy-photo{left:490px;top:1519px;width:710px;height:521px;background:linear-gradient(90deg,rgba(221,225,239,1) 0%,#a9b4cb 25%,#5d6c86 55%,#2d3c56 100%)}
.strategy-kicker{left:164px;top:1640px;font-family:'Montserrat',sans-serif;font-weight:700;font-size:31px;color:var(--red)}
.strategy-title{left:164px;top:1686px;font-size:27px}
.strategy-text{left:164px;top:1736px;width:400px;font-size:17px;line-height:27px;color:#444}

/* news */
.news-heading{left:162px;top:2125px;font-size:28px}
.news{top:2186px;width:274px;height:383px;background:var(--white);border-top:4px solid var(--red);box-shadow:0 1px 5px rgba(0,0,0,.15)}
.news-date{position:absolute;left:11px;top:16px;width:50px;height:56px;background:var(--red);clip-path:polygon(50% 0,100% 25%,100% 75%,50% 100%,0 75%,0 25%);color:var(--white);text-align:center;font-family:'Montserrat',sans-serif;padding-top:9px}
.news-date b{display:block;font-size:20px;line-height:20px;font-weight:600}
.news-date span{font-size:11px}
.news-title{position:absolute;left:74px;top:28px;font-size:16px;line-height:21px;color:#222;font-weight:700}
.news-img{position:absolute;left:0;top:96px;width:274px;height:159px}
.news p{position:absolute;left:24px;top:273px;width:232px;font-size:12px;line-height:16px;color:#666}
.news a{position:absolute;left:24px;top:340px;font-family:'Montserrat',sans-serif;font-weight:700;font-size:13px;color:var(--red);text-decoration:none}

/* testimonials */
.testi{left:0;top:2642px;width:1200px;height:388px;background:linear-gradient(180deg,#9a1f33,#8a1a2c)}
.testi-title{left:0;top:2722px;width:1176px;text-align:center;font-family:'Lato',sans-serif;font-weight:700;font-size:34px;color:var(--white)}
.quote{left:0;top:2780px;width:1176px;text-align:center;font-family:Georgia,serif;font-size:80px;line-height:70px;color:rgba(255,255,255,.35)}
.testi-text{left:290px;top:2830px;width:600px;text-align:center;font-size:18px;line-height:27px;color:var(--white)}
.testi-name{left:0;top:2930px;width:1160px;text-align:center;font-family:'Lato',sans-serif;font-weight:700;font-size:20px;color:var(--white)}

/* footer */
.footer{left:0;top:3030px;width:1200px;height:395px;background:var(--footer)}
.fcol{top:3104px;color:var(--footer-text);font-size:14px}
.fcol h4{font-family:'Montserrat',sans-serif;font-weight:600;font-size:16px;color:var(--white);text-transform:uppercase;margin-bottom:16px}
.fcol li{list-style:none;line-height:28px}
.fcol .row{display:flex;gap:12px;align-items:flex-start;margin-bottom:14px;line-height:18px}
.soc-sq{width:13px;height:13px;background:var(--footer-text);margin-top:3px;flex:none}
.footer-rule{left:0;top:3356px;width:1200px;height:1px;background:#333}
.copyright{left:0;top:3376px;width:1200px;text-align:center;font-size:14px;color:#8a8a8a}
</style>
</head>
<body>

<!-- header -->
<div class="abs topbar">
  <svg width="18" height="18" viewBox="0 0 24 24"><path fill="#fff" d="M6.6 10.8a15.1 15.1 0 0 0 6.6 6.6l2.2-2.2a1 1 0 0 1 1-.25 11.4 11.4 0 0 0 3.6.57 1 1 0 0 1 1 1V20a1 1 0 0 1-1 1A17 17 0 0 1 3 4a1 1 0 0 1 1-1h3.5a1 1 0 0 1 1 1c0 1.25.2 2.45.57 3.57a1 1 0 0 1-.25 1z"/></svg>
  CALL US 01-555-0190
</div>
<div class="abs brand"><span>Bork Ventures</span><span class="brand-square"></span></div>
<div class="abs nav-dot"></div>
<nav class="abs nav">
  <span class="active">HOME</span><span>ABOUT US</span><span>SERVICES</span><span>STRATEGY</span><span>IT NEWS</span><span>CONTACT US</span>
</nav>

<!-- hero -->
<div class="abs hero" role="img" aria-label="Glowing data centre server racks with code overlay"></div>
<div class="abs hero-title">WELCOME TO BORK VENTURES</div>
<div class="abs hero-sub">MISSION INTEGRITY RESULTS</div>
<div class="abs hero-btn">GET STARTED</div>
<div class="abs circle-arrow" style="left:74px;top:359px"><svg width="20" height="20" viewBox="0 0 20 20"><path d="M13 3 6 10l7 7" stroke="#111" stroke-width="2.5" fill="none"/></svg></div>
<div class="abs circle-arrow" style="left:1079px;top:353px"><svg width="20" height="20" viewBox="0 0 20 20"><path d="M7 3l7 7-7 7" stroke="#111" stroke-width="2.5" fill="none"/></svg></div>

<!-- services -->
<div class="abs band"></div>
<svg class="abs" style="left:106px;top:818px" width="30" height="56"><path d="M26 2 4 28l22 26" stroke="#666" stroke-width="2" fill="none"/></svg>
<svg class="abs" style="left:1072px;top:818px" width="30" height="56"><path d="M4 2l22 26L4 54" stroke="#666" stroke-width="2" fill="none"/></svg>

<div class="abs svc" style="left:167px">
  <div class="svc-head">Hardware /<br>Software Sales</div>
  <div class="svc-img" role="img" aria-label="Illuminated processor chip on a circuit board" style="background:radial-gradient(circle at 55% 65%,#dfe9ff 0%,#5f7fb0 18%,#1c2433 55%,#0d1118 100%)"></div>
  <p>We have access to multiple distributor partners throughout North America, as well as Elite Partner Status</p>
  <div class="btn-outline">Learn More</div>
</div>
<div class="abs svc" style="left:463px">
  <div class="svc-head">Professional<br>Services</div>
  <div class="svc-img" role="img" aria-label="Technician working among server racks" style="background:linear-gradient(90deg,#1a1d22,#3d434c 50%,#1c1f24)"></div>
  <p>Our team provides experienced leader-ship and guidance, utilizing the industry standard methodologies.</p>
  <div class="btn-outline">Learn More</div>
</div>
<div class="abs svc" style="left:758px">
  <div class="svc-head">Technology<br>Assessment</div>
  <div class="svc-img" role="img" aria-label="Hand touching a blue digital interface" style="background:linear-gradient(135deg,#0b1f3c,#1f6fb7 55%,#0c2a52)"></div>
  <p>Experience has shown companies that perform objective, third-party technol-ogy assessments have proveN</p>
  <div class="btn-outline">Learn More</div>
</div>

<!-- intro -->
<div class="abs intro-mark"></div>
<h2 class="abs head intro-title">Bringing thought leadership and<br>quality to every project</h2>
<p class="abs intro-text">Bork Ventures, Inc. is an 8(a) full-service IT consulting company based in the Washington, DC Metro area. We offer specialized, highly customized technology solutions for our customers located throughout the United States</p>
<div class="btn-outline" style="left:518px;top:1391px;width:166px;height:48px">Learn More</div>

<!-- strategy -->
<div class="abs strategy"></div>
<div class="abs strategy-photo" role="img" aria-label="Team of colleagues collaborating around an office table"></div>
<div class="abs strategy-kicker">OUR STRATEGY</div>
<h2 class="abs head strategy-title">Your path to success</h2>
<p class="abs strategy-text">Civilian and Federal agencies are facing increased demands driven by the changing economic environment and shifts in the way products and services are sold and delivered.</p>
<div class="btn-outline" style="left:167px;top:1871px;width:172px;height:49px">Learn More</div>

<!-- news -->
<h2 class="abs head news-heading">Latest news</h2>
<div class="abs news" style="left:158px">
  <div class="news-date"><b>02</b><span>JAN</span></div>
  <div class="news-title">Pellentesque faucibus<br>Ut accumsan ultric</div>
  <div class="news-img" role="img" aria-label="Abstract network of connected points" style="background:radial-gradient(circle at 40% 40%,#3b5a9a,#101a33 70%)"></div>
  <p>Duis quam Nam eget lacus Aliquam erat volutpat Quisque dignissim congue leo Mauris vel lacus vitae felis vestibulum</p>
  <a>READ MORE</a>
</div>
<div class="abs news" style="left:463px">
  <div class="news-date"><b>10</b><span>JAN</span></div>
  <div class="news-title">Pellentesque faucibus<br>Ut accumsan ultric</div>
  <div class="news-img" role="img" aria-label="Engineer cabling a network switch" style="background:linear-gradient(90deg,#5d6672,#c9d0da 60%,#e8ecf2)"></div>
  <p>Duis quam Nam eget lacus Aliquam erat volutpat Quisque dignissim congue leo Mauris vel lacus vitae felis vestibulum</p>
  <a>READ MORE</a>
</div>
<div class="abs news" style="left:769px">
  <div class="news-date"><b>20</b><span>JAN</span></div>
  <div class="news-title">Pellentesque faucibus<br>Ut accumsan ultric</div>
  <div class="news-img" role="img" aria-label="Technician inspecting a server room" style="background:linear-gradient(90deg,#2a3340,#6b7685 50%,#aab3bf)"></div>
  <p>Duis quam Nam eget lacus Aliquam erat volutpat Quisque dignissim congue leo Mauris vel lacus vitae felis vestibulum</p>
  <a>READ MORE</a>
</div>

<!-- testimonials -->
<div class="abs testi"></div>
<div class="abs testi-title">Testimonials</div>
<div class="abs quote">&#8220;</div>
<p class="abs testi-text">Sed ut perspiciatis unde omnis iste natus error sit voluptatem accusantium doloremque laudantium, totam rem aperiam, eaque ipsa quae ab illo inventore veritatis et quasi architecto</p>
<div class="abs testi-name">DANA WHITFIELD</div>
<svg class="abs" style="left:150px;top:2830px" width="48" height="30"><path d="M46 15H3M16 2 3 15l13 13" stroke="#fff" stroke-width="2.5" fill="none"/></svg>
<svg class="abs" style="left:960px;top:2830px" width="48" height="30"><path d="M2 15h43M32 2l13 13-13 13" stroke="#fff" stroke-width="2.5" fill="none"/></svg>

<!-- footer -->
<div class="abs footer"></div>
<div class="abs fcol" style="left:359px">
  <h4>Company</h4>
  <ul><li>Home</li><li>About us</li><li>Our Services</li><li>Why Us</li><li>Strategy</li></ul>
</div>
<div class="abs fcol" style="left:510px">
  <h4>Resources</h4>
  <ul><li>News</li><li>Testimonials</li><li>Term of Use</li><li>Sitemap</li><li>Contact Us</li></ul>
</div>
<div class="abs fcol" style="left:668px">
  <h4>Contact us</h4>
  <div class="row"><svg width="16" height="18" viewBox="0 0 16 18"><path d="M8 17s6-6 6-10A6 6 0 0 0 2 7c0 4 6 10 6 10z" stroke="#bdbdbd" stroke-width="1.5" fill="none"/><circle cx="8" cy="7" r="2" fill="#bdbdbd"/></svg><span>2250 Larkfield Ct<br>Ashmont, MD 20999</span></div>
  <div class="row"><svg width="16" height="16" viewBox="0 0 24 24"><path d="M6.6 10.8a15.1 15.1 0 0 0 6.6 6.6l2.2-2.2a1 1 0 0 1 1-.25 11.4 11.4 0 0 0 3.6.57 1 1 0 0 1 1 1V20a1 1 0 0 1-1 1A17 17 0 0 1 3 4a1 1 0 0 1 1-1h3.5a1 1 0 0 1 1 1c0 1.25.2 2.450.57 3.57a1 1 0 0 1-.25 1z" stroke="#bdbdbd" stroke-width="1.6" fill="none"/></svg><span>301-555-0190</span></div>
  <div class="row"><svg width="16" height="14" viewBox="0 0 16 14"><rect x="1" y="1" width="14" height="12" stroke="#bdbdbd" stroke-width="1.4" fill="none"/><path d="M1 2l7 6 7-6" stroke="#bdbdbd" stroke-width="1.4" fill="none"/></svg><span>info@borkventures.example</span></div>
</div>
<div class="abs fcol" style="left:901px">
  <h4>Social media</h4>
  <div class="row"><span class="soc-sq"></span><span>Townsquare</span></div>
  <div class="row"><span class="soc-sq"></span><span>Chirrup</span></div>
  <div class="row"><span class="soc-sq"></span><span>Worknet</span></div>
  <div class="row"><span class="soc-sq"></span><span>Picturebox</span></div>
</div>
<div class="abs footer-rule"></div>
<div class="abs copyright">© 2019 Company Name&nbsp; All right reserved</div>

</body>
</html>
```